Verodex business card

Business card for sustainable investment company called "Verodex". Verodex is an exchange platform selling carbon credits between buyers and sellers. Carbon Credits are an environmental commodity for reducing global carbon emissions.

the card should obviously have our logo and the theme should be sustainability/environment mixed with a trading platform.

Contact Information for Business Card

Logo, Name, Title, Phone, Email

Colors
0054AA
0677BA
7BADD7
CADEEF
E8F1F8
0094D4
00A9DD
6FCCEA
C7EBF8
E9F6FB
00AB8E
00BBA5
67D7C9
C6EFE9
E9F9F6
59FF00
82FF00
B8FF75
E3FFCB
F4FFEA

```html
<!DOCTYPE html>
<html lang="en">
<head>
<meta charset="utf-8">
<title>Verodex business card</title>
<link href="https://fonts.googleapis.com/css2?family=Montserrat:wght@400;500;600;700&display=swap" rel="stylesheet">
<style>
  :root {
    --page-bg: #e8e9eb;
    --navy: #172a52;
    --white: #ffffff;
    --sky: #2fb4e8;
    --blue: #4677c0;
    --aqua: #5ccbe3;
    --ink: #1d1d1f;
    --faint: #eef2fa;
  }
  * { box-sizing: border-box; margin: 0; padding: 0; }
  html, body {
    width: 1200px; height: 900px; overflow: hidden;
    background: var(--page-bg);
    font-family: "Montserrat", sans-serif;
  }
  .sheet {
    position: relative; width: 1200px; height: 900px;
    display: flex; flex-direction: column; align-items: center; justify-content: center; gap: 36px;
  }
  .card {
    position: relative; width: 700px; height: 400px; overflow: hidden;
    box-shadow: 0 6px 18px rgba(0,0,0,0.12);
  }
  .card--front { background: var(--navy); display: flex; align-items: center; justify-content: center; }
  .card--back { background: var(--white); }

  .brand { display: flex; align-items: center; gap: 22px; }
  .brand__dot { border-radius: 50%; background: var(--sky); flex: none; }
  .brand__name { font-weight: 600; letter-spacing: 0.04em; text-transform: uppercase; line-height: 1; }

  .card--front .brand__dot { width: 82px; height: 82px; }
  .card--front .brand__name { font-size: 74px; color: var(--white); }

  .card--back .brand { position: absolute; left: 62px; top: 90px; gap: 16px; z-index: 2; }
  .card--back .brand__dot { width: 52px; height: 52px; }
  .card--back .brand__name { font-size: 44px; color: var(--navy); }

  .backdrop-circle {
    position: absolute; right: 40px; top: 30px; width: 220px; height: 220px;
    border-radius: 50%; background: var(--faint);
  }
  .person { position: absolute; right: 70px; top: 92px; text-align: right; z-index: 2; }
  .person__name { font-size: 27px; font-weight: 700; color: var(--navy); letter-spacing: 0.02em; line-height: 1.2; }
  .person__name span { color: var(--sky); }
  .person__title { font-size: 17px; font-weight: 500; color: var(--ink); margin-top: 4px; line-height: 1.2; }

  .contacts { position: absolute; left: 62px; top: 218px; list-style: none; z-index: 2; }
  .contacts li { display: flex; align-items: center; gap: 12px; font-size: 19px; color: var(--ink); line-height: 32px; }
  .contacts svg { width: 20px; height: 20px; flex: none; }

  .wave { position: absolute; left: 0; top: 0; width: 700px; height: 400px; z-index: 1; }
</style>
</head>
<body>
<main class="sheet">
  <section class="card card--front" aria-label="Card front">
    <div class="brand">
      <span class="brand__dot"></span>
      <span class="brand__name">Verodex</span>
    </div>
  </section>

  <section class="card card--back" aria-label="Card back">
    <div class="backdrop-circle"></div>
    <svg class="wave" viewBox="0 0 700 400" aria-hidden="true">
      <defs>
        <linearGradient id="band" x1="0" y1="1" x2="1" y2="0">
          <stop offset="0" stop-color="#5ccbe3"/>
          <stop offset="0.5" stop-color="#2fb4e8"/>
          <stop offset="1" stop-color="#4677c0"/>
        </linearGradient>
      </defs>
      <path d="M0 400 C 260 385, 390 355, 490 292 S 630 212, 700 210 L700 400 Z" fill="url(#band)"/>
      <path d="M0 385 C 260 368, 390 338, 490 274 S 630 196, 700 194" fill="none" stroke="#172a52" stroke-width="7"/>
    </svg>

    <div class="brand">
      <span class="brand__dot"></span>
      <span class="brand__name">Verodex</span>
    </div>

    <div class="person">
      <p class="person__name">DANIEL <span>KELLER</span></p>
      <p class="person__title">Co-Founder</p>
    </div>

    <ul class="contacts">
      <li>
        <svg viewBox="0 0 24 24"><path fill="#2fb4e8" d="M6.6 10.8a15 15 0 0 0 6.6 6.6l2.2-2.2c.3-.3.7-.4 1-.2 1.1.4 2.3.6 3.6.6.6 0 1 .4 1 1V20c0 .6-.4 1-1 1A17 17 0 0 1 3 4c0-.6.4-1 1-1h3.5c.6 0 1 .4 1 1 0 1.3.2 2.5.6 3.6.1.3 0 .7-.2 1z"/></svg>
        555-210-4836
      </li>
      <li>
        <svg viewBox="0 0 24 24"><rect x="2" y="5" width="20" height="14" rx="2" fill="#2fb4e8"/><path d="M3 6l9 7 9-7" fill="none" stroke="#fff" stroke-width="1.6"/></svg>
        info@verodex.com
      </li>
      <li>
        <svg viewBox="0 0 24 24"><circle cx="12" cy="12" r="10" fill="#2fb4e8"/><path d="M2 12h20M12 2c3 3 3 17 0 20M12 2c-3 3-3 17 0 20" fill="none" stroke="#fff" stroke-width="1.3"/></svg>
        www.verodex.com
      </li>
    </ul>
  </section>
</main>
</body>
</html>
```